Creation of an elegant and modern turnkey Shopify website

Hello,

We are a new company specializing in the sale of above-ground pools. We want to create a turnkey website, ideally using Shopify. For now, we need a "showcase" site, not an e-commerce platform, with four tabs:

Home Page (an overall presentation of the company)
Our Products (an overview of all the above-ground pools we sell)
Our Projects (a page inspired by Instagram to showcase photos of our future projects)
Contact (a page with all our contact information and a contact form)

We are looking to create a highly visual, elegant, and modern website with vibrant splashes of color. We will provide the text, photos (along with instructions on where to place them on each page), and all other necessary information as attachments.

Thank you in advance for your proposals!

The Brisa Lagoon Team

Target Market(s)

Targeted at Swiss customers (a translator will need to be installed for different languages)

Industry/Entity Type

Sale of customised above-ground pools

Coding

Coded - Design and coding required

Font styles to use
Sans Serif

Colors
0094D4
00A9DD
6FCCEA
C7EBF8
E9F6FB
00AB8E
00BBA5
67D7C9
C6EFE9
E9F9F6

Requirements
Must have
• A stunning, elegant and modern look
Nice to have
• Inspiration from the colors of our logo throughout the site, but in an elegant way
Should not have
• An overly classic look for swimming pool sites

```html
<!DOCTYPE html>
<html lang="en">
<head>
<meta charset="utf-8">
<title>Brisa Lagoon – Above-Ground Pools</title>
<link href="https://fonts.googleapis.com/css2?family=Plus+Jakarta+Sans:wght@300;400;500;600&display=swap" rel="stylesheet">
<style>
:root{
  --nav:#c0f8fd;
  --panel:#effdfd;
  --accent:#12c2cf;
  --button:#05e0ee;
  --ink:#2b2b2b;
  --muted:#555;
  --logo-grey:#7a7a7a;
  --white:#ffffff;
  --footer:#bdf7fc;
}
*{box-sizing:border-box;margin:0;padding:0}
html,body{width:1200px;height:4100px;overflow:hidden}
body{font-family:"Plus Jakarta Sans",sans-serif;background:var(--white);color:var(--ink);position:relative}
.abs{position:absolute}
.media{position:absolute}
.panel{position:absolute;background:var(--panel)}
.btn{display:flex;align-items:center;justify-content:center;gap:10px;background:var(--button);color:var(--white);font-size:16px;font-weight:600;height:46px;text-transform:uppercase;letter-spacing:.2px}
.btn svg{width:10px;height:14px}
.rule{height:5px;background:var(--accent)}

/* nav */
.nav{left:0;top:0;width:1200px;height:77px;background:var(--nav)}
.nav-brand{left:76px;top:14px;width:70px;font-size:17px;font-weight:300;color:var(--logo-grey);line-height:22px;text-transform:uppercase}
.nav-links{left:396px;top:30px;display:flex;gap:22px;font-size:13px;font-weight:500;color:#333}
.nav-links span{padding:0 0 10px}
.nav-links .active{border-bottom:2px solid #333;padding:0 10px 10px}
.lang{left:1043px;top:29px;display:flex;align-items:center;gap:8px;font-size:13px;font-weight:500}
.lang i{width:18px;height:18px;border-radius:50%;background:#c6354a;display:block}

/* row 1 */
.welcome{left:699px;top:111px;width:434px;height:599px;text-align:center}
.welcome h3{margin-top:85px;font-size:30px;font-weight:400}
.welcome .brand{margin-top:28px;font-size:60px;font-weight:300;line-height:74px;color:var(--logo-grey);text-transform:uppercase}
.welcome .rule{width:156px;margin:24px auto 0}
.welcome p{margin-top:30px;font-size:17px;line-height:29px}
.welcome .btn{margin:28px auto 0;width:368px}

/* row 2 */
.dream{left:67px;top:729px;width:433px;height:598px;text-align:center}
.dream h2{margin-top:90px;font-size:44px;line-height:58px;font-weight:500;color:var(--accent);padding:0 30px}
.dream .rule{width:100px;margin:22px auto 0}
.dream p{margin-top:28px;font-size:17px;line-height:29px;padding:0 60px}
.dream .btn{margin:32px auto 0;width:368px}

/* banner */
.banner-box{left:167px;top:1397px;width:866px;height:362px;background:rgba(235,250,252,.75);text-align:center}
.banner-box h2{margin-top:42px;font-size:41px;font-weight:500;letter-spacing:-.5px}
.banner-box .rule{width:334px;margin:22px auto 0}
.banner-box p{margin:30px auto 0;width:730px;font-size:17px;line-height:29px}
.banner-actions{display:flex;justify-content:center;gap:17px;margin-top:20px}
.banner-actions .btn{width:300px}

/* features */
.features{padding-left:25px}
.features h2{border-left:5px solid var(--accent);padding-left:28px;font-size:43px;line-height:58px;font-weight:600;color:var(--accent);text-transform:uppercase}
.feature{border-left:4px solid var(--accent);margin-top:36px;padding-left:18px}
.feature h4{font-size:30px;font-weight:500;color:var(--accent)}
.feature p{margin-top:10px;font-size:17px;line-height:29px;color:var(--ink)}
.why{left:67px;top:1829px;width:523px;height:598px;padding-top:62px}
.also{left:608px;top:2445px;width:525px;height:600px;padding-top:54px}
.also .feature{margin-top:30px}
.also .feature p{font-size:16.5px}

/* dreams band */
.band{left:67px;top:3062px;width:1066px;height:86px;background:var(--panel);text-align:center;font-size:41px;font-weight:500;line-height:86px;color:var(--accent);text-transform:uppercase;letter-spacing:-.5px}

/* cards */
.card{position:absolute;top:3162px;width:344px;height:527px;background:var(--panel)}
.card .media{left:0;top:0;width:344px;height:264px}
.card h4{position:absolute;left:17px;top:292px;width:310px;font-size:25px;line-height:34px;font-weight:600;text-transform:uppercase;color:#333;padding-bottom:14px;border-bottom:4px solid var(--accent)}
.card p{position:absolute;left:17px;top:392px;width:310px;font-size:16.5px;line-height:29px;color:var(--muted)}

/* footer */
.footer{left:0;top:3708px;width:1200px;height:392px;background:var(--footer)}
.footer-brand{left:106px;top:58px;width:180px;font-size:60px;font-weight:300;line-height:72px;color:var(--logo-grey);text-transform:uppercase}
.socials{left:113px;top:250px;display:flex;gap:16px}
.socials i{width:27px;height:27px;border:3px solid #333;border-radius:50%;display:block}
.footer h5{font-size:23px;font-weight:600;line-height:28px;text-transform:uppercase;color:#333}
.footer-contact{left:446px;top:62px;font-size:16px;line-height:29px}
.footer-contact address{font-style:normal;margin-top:20px}
.footer-contact .phone{display:flex;align-items:center;gap:10px}
.subscribe{left:788px;top:62px;width:336px;font-size:16px;line-height:29px}
.subscribe p{margin-top:12px}
.subscribe-form{display:flex;margin-top:14px}
.subscribe-form span{flex:1;height:36px;background:var(--white);font-size:12px;color:#999;padding:0 10px;line-height:36px}
.subscribe-form b{width:84px;height:36px;background:var(--button);color:var(--white);font-size:13px;font-weight:600;line-height:36px;text-align:center}
.footer-rule{left:67px;top:314px;width:1066px;height:3px;background:var(--accent)}
.copyright{left:67px;top:332px;font-size:10px;color:#333}
</style>
</head>
<body>

<header class="abs nav">
  <div class="abs nav-brand">Brisa Lagoon</div>
  <nav class="abs nav-links">
    <span class="active">HOME</span><span>OUR PRODUCTS</span><span>OUR PROJECTS</span><span>CONTACT</span>
  </nav>
  <div class="abs lang"><i></i>ENG
    <svg width="12" height="8" viewBox="0 0 12 8"><path d="M0 0h12L6 8z" fill="#333"/></svg>
  </div>
</header>

<div class="media" style="left:67px;top:111px;width:614px;height:599px;background:linear-gradient(160deg,#7fd8e6,#b7eef4 45%,#4fc3d4)" role="img" aria-label="Legs of a woman in a sun hat floating in clear turquoise water"></div>
<section class="panel welcome">
  <h3>Welcome To</h3>
  <div class="brand">Brisa<br>Lagoon</div>
  <div class="rule"></div>
  <p>Transform Your Garden with Our Premium<br>Above-Ground Pools!</p>
  <div class="btn">Contact Us <svg viewBox="0 0 10 14"><path d="M2 1l6 6-6 6" stroke="#fff" stroke-width="2.4" fill="none"/></svg></div>
</section>

<section class="panel dream">
  <h2>Have You Ever Dreamt of Relaxing in The Middle of A Pool?</h2>
  <div class="rule"></div>
  <p>Achieve your dreams with our custom, tailor-made above-ground pools.</p>
  <div class="btn">Contact Us <svg viewBox="0 0 10 14"><path d="M2 1l6 6-6 6" stroke="#fff" stroke-width="2.4" fill="none"/></svg></div>
</section>
<div class="media" style="left:519px;top:729px;width:614px;height:598px;background:linear-gradient(135deg,#a6e6ee,#7dd6e3 55%,#c9eff2)" role="img" aria-label="Aerial view of a woman on a pink float ring in a clear pool"></div>

<div class="media" style="left:67px;top:1345px;width:1066px;height:465px;background:linear-gradient(120deg,#a7e4ee,#cdf2f6 50%,#8fd9e6)" role="img" aria-label="Rippling light blue pool water"></div>
<section class="abs banner-box">
  <h2>BRING HAPPINESS THROUGH CHANGE</h2>
  <div class="rule"></div>
  <p>Imagine an exceptional relaxation and leisure space right in your own backyard. With our unparalleled expertise and commitment to excellence, we create above-ground pools that exceed all expectations. Our exclusive, custom-designed models are crafted to combine style, durability, and innovation, offering a unique and refined experience.</p>
  <div class="banner-actions">
    <div class="btn">Contact Us <svg viewBox="0 0 10 14"><path d="M2 1l6 6-6 6" stroke="#fff" stroke-width="2.4" fill="none"/></svg></div>
    <div class="btn">Learn More <svg viewBox="0 0 10 14"><path d="M2 1l6 6-6 6" stroke="#fff" stroke-width="2.4" fill="none"/></svg></div>
  </div>
</section>

<section class="panel why features">
  <h2>Why choose our above-ground pools?</h2>
  <div class="feature"><h4>Superior Quality</h4><p>Each pool is constructed with high-quality materials,<br>ensuring exceptional durability and strength.</p></div>
  <div class="feature"><h4>Elegant Design</h4><p>Our pools come in a variety of styles and finishes,<br>seamlessly blending into any garden setting.</p></div>
</section>
<div class="media" style="left:608px;top:1829px;width:525px;height:598px;background:linear-gradient(160deg,#3fb8b4,#14a6a2 55%,#5fa6a2)" role="img" aria-label="Aerial view of a long teal pool with wooden decking and a person on a lounger"></div>

<div class="media" style="left:67px;top:2445px;width:523px;height:600px;background:linear-gradient(120deg,#4fc4dc,#7fd6e6 60%,#c9ecef)" role="img" aria-label="Woman in a sun hat walking beside sparkling blue pool water"></div>
<section class="panel also features">
  <h2>And also...</h2>
  <div class="feature"><h4>Custom and Tailor-Made</h4><p>Create the pool of your dreams with our customization options, tailored to your specific tastes and needs.</p></div>
  <div class="feature"><h4>Easy Installation</h4><p>Enjoy your new oasis quickly with our simple and fast installation process.</p></div>
  <div class="feature"><h4>Constant Innovation</h4><p>We incorporate the latest technologies to provide you with an optimal and safe swimming experience.</p></div>
</section>

<div class="abs band">We bring your pool dreams to life!</div>

<article class="card" style="left:67px">
  <div class="media" style="background:linear-gradient(135deg,#f2f2f2,#d9d9d9)" role="img" aria-label="Consultant in a white blazer holding a tablet"></div>
  <h4>Personalized<br>Services</h4>
  <p>We understand that every garden and client is unique. That's why we offer personalized services, from design to installation and after-sales support.</p>
</article>
<article class="card" style="left:427px">
  <div class="media" style="background:linear-gradient(135deg,#8a8478,#d4d0c8)" role="img" aria-label="Hand stamping a signed document on a desk"></div>
  <h4>Guaranteed<br>Satisfaction</h4>
  <p>Join our community of satisfied customers who are already enjoying their custom above-ground pools. 10-Year Warranty!</p>
</article>
<article class="card" style="left:788px">
  <div class="media" style="background:linear-gradient(135deg,#2c3e48,#1a262c)" role="img" aria-label="Vintage rotary telephone on a dark table"></div>
  <h4>Contact Us<br>Today</h4>
  <p>Contact us today to discover our range of customizable above-ground pools and get a tailored quote. Dive into infinite possibilities with Brisa Lagoon.</p>
</article>

<footer class="abs footer">
  <div class="abs footer-brand">Brisa Lagoon</div>
  <div class="abs socials" aria-label="Social media links"><i></i><i></i><i></i><i></i></div>
  <div class="abs footer-contact">
    <h5>Contact Us<br>Brisa Lagoon</h5>
    <address>Lucien Maret<br>Chemin des Saules 12<br>1860 Aigle</address>
    <div style="margin-top:8px">Contact Us</div>
    <div class="phone"><svg width="16" height="16" viewBox="0 0 24 24"><path d="M6.6 10.8a15 15 0 0 0 6.6 6.6l2.2-2.2c.3-.3.7-.4 1-.2 1.1.4 2.3.6 3.6.6.6 0 1 .4 1 1V20c0 .6-.4 1-1 1A17 17 0 0 1 3 4c0-.6.4-1 1-1h3.5c.6 0 1 .4 1 1 0 1.3.2 2.5.6 3.6.1.3 0 .7-.2 1z" fill="#222"/></svg>079 000 12 34</div>
  </div>
  <div class="abs subscribe">
    <h5>Subscribe</h5>
    <p>Enter your email address to register to our newsletter subscription</p>
    <div class="subscribe-form"><span>Enter e-mail address</span><b>Subscribe</b></div>
  </div>
  <div class="abs footer-rule"></div>
  <div class="abs copyright">© 2024 Brisa Lagoon. All rights reserved.</div>
</footer>

</body>
</html>
```